Constant Contact email marketing template

I need engaging customizable templates that can be used in multiple fundraising campaigns.

I included a school bus project that we used in a previous campaign. This campaign, however, is a $25 for $25 promotion. Consumers make a $25 contribution for the school or charity and receive back a $25 e-gift card to be used at area restaurants.

Important! This is a completely generic piece, capable of being used in schools, churches, or other civic organizations.

The 5 part example is NOT what I am looking for. I included it to suggest the concept. I am looking forward to viewing YOUR designs,

Target Market(s)

schools, leagues, nonprofit organizations

Font styles to use
Sans Serif

Colors

Designer to choose colors to be used in the design.

Requirements
Must have
• Must clearly present itself as a fundraising tool for schools, leagues and Nonprofit organizations.
• Must have 2 clickable buttons that allow member to click

```html
<!DOCTYPE html>
<html lang="en">
<head>
<meta charset="utf-8">
<title>Greatest Fundraiser Ever – $25 for $25</title>
<link rel="stylesheet" href="https://fonts.googleapis.com/css2?family=Bebas+Neue&family=Kaushan+Script&family=Oswald:wght@300;400&family=Open+Sans:wght@700;800&family=PT+Sans+Narrow:wght@400;700&family=Yellowtail&display=swap">
<style>
  :root{
    --black:#000;
    --white:#fff;
    --red:#e2322b;
    --red-deep:#c81f25;
    --orange:#f47a20;
    --orange-light:#f9a13a;
    --gold:#f6b318;
    --yellow:#f8d21c;
    --text-dark:#262626;
    --tick:#c41e24;
    --card-shadow:rgba(0,0,0,.28);
  }
  *{margin:0;padding:0;box-sizing:border-box}
  html,body{width:1200px;height:2765px;overflow:hidden;background:var(--white)}
  .canvas{position:relative;width:1200px;height:2765px;overflow:hidden;font-family:"Open Sans",Arial,sans-serif}
  .backdrop,.offer-card{position:absolute;left:0;top:0}

  .brand{position:absolute;top:110px;left:0;width:1200px;text-align:center;color:var(--white);
    font-family:"Oswald",sans-serif;font-weight:400;font-size:56px;letter-spacing:3px;line-height:1}
  .brand-sub{display:block;font-size:21px;letter-spacing:9px;margin-top:14px}

  .tagline{position:absolute;right:70px;top:400px;text-align:right;color:var(--white)}
  .tagline .greatest{display:block;font-family:"Yellowtail",cursive;font-size:64px;line-height:1;margin-right:20px}
  .tagline .fundraiser{display:block;font-family:"Bebas Neue",sans-serif;color:var(--gold);font-size:52px;letter-spacing:16px;line-height:1;margin-top:2px}
  .tagline .ever{display:block;font-family:"Kaushan Script",cursive;font-size:92px;line-height:1;margin-right:-10px}

  .card-word{position:absolute;font-family:"Kaushan Script",cursive;color:var(--red-deep);line-height:1;white-space:nowrap}
  .card-donate{left:166px;top:1020px;font-size:100px;transform:rotate(-5deg)}
  .card-get{left:315px;top:1140px;font-size:104px;transform:rotate(-5deg)}
  .card-amount{position:absolute;font-family:"Bebas Neue",sans-serif;color:var(--white);line-height:1}
  .amount-top{left:570px;top:995px;font-size:112px;transform:rotate(-4deg)}
  .amount-bottom{left:885px;top:1325px;font-size:150px}
  .card-amount small{font-size:.6em;vertical-align:.38em}
  .egift{position:absolute;left:525px;top:1360px;width:275px;height:115px;border:3px solid var(--text-dark);text-align:center;background:var(--white)}
  .egift-word{display:block;font-family:"Kaushan Script",cursive;color:var(--red-deep);font-size:70px;line-height:1;margin-top:6px}
  .egift-label{position:absolute;left:50%;bottom:-17px;transform:translateX(-50%);background:var(--white);padding:0 10px;
    font-family:"Bebas Neue",sans-serif;color:var(--red-deep);font-size:30px;letter-spacing:8px;line-height:1}

  .cta{position:absolute;display:block;width:420px;height:420px;border-radius:50%;text-decoration:none;
    background:linear-gradient(180deg,#f6f6f6,#b9b9b9);box-shadow:0 10px 24px rgba(0,0,0,.25)}
  .cta-face{position:absolute;left:20px;top:20px;width:380px;height:380px;border-radius:50%;text-align:center}
  .cta-red{left:30px;top:1560px}
  .cta-red .cta-face{background:radial-gradient(circle at 50% 35%,#f0502a,var(--red-deep));color:var(--white)}
  .cta-gold{left:48px;top:2214px}
  .cta-gold .cta-face{background:radial-gradient(circle at 50% 35%,var(--yellow),var(--gold));color:var(--red-deep)}
  .cta-label{position:absolute;left:0;top:96px;width:380px;font-family:"Bebas Neue",sans-serif;font-size:48px;letter-spacing:4px;line-height:1}
  .cta-red .cta-label{color:var(--gold)}
  .cta-gold .cta-label{color:var(--red-deep)}
  .cta-price{position:absolute;left:140px;font-family:"Oswald",sans-serif;font-weight:300;font-size:118px;line-height:1}
  .cta-price sup{font-size:42px;vertical-align:top;position:relative;top:14px;margin-right:2px}
  .price-one{top:140px}
  .price-two{top:236px}
  .cta-for{position:absolute;left:92px;top:210px;font-family:"Bebas Neue",sans-serif;font-size:32px;line-height:1}

  .pitch{position:absolute;left:483px;top:1650px;width:700px;font-weight:800;font-size:47px;line-height:48px;color:var(--text-dark);letter-spacing:-.3px}

  .benefits{position:absolute;left:168px;top:1984px;list-style:none}
  .benefits li{font-family:"PT Sans Narrow",sans-serif;font-weight:700;font-size:34px;color:var(--tick);line-height:50px;height:50px;display:flex;align-items:center;white-space:nowrap}
  .benefits svg{width:34px;height:34px;margin-right:6px;flex:none}

  .upsell-title{position:absolute;left:457px;top:2292px;font-weight:800;font-size:70px;color:var(--red);line-height:1;white-space:nowrap}
  .upsell-text{position:absolute;left:459px;top:2393px;width:460px;font-family:"PT Sans Narrow",sans-serif;font-weight:400;font-size:30px;line-height:44px;color:var(--text-dark)}

  .contact{position:absolute;right:40px;top:2640px;color:var(--white);font-weight:700;font-size:28px;line-height:50px}
  .contact a{color:var(--white);text-decoration:none;display:flex;align-items:center;justify-content:flex-end}
  .contact svg{width:42px;height:42px;margin-left:14px}
</style>
</head>
<body>
<div class="canvas">
  <svg class="backdrop" width="1200" height="2765" viewBox="0 0 1200 2765">
    <defs>
      <linearGradient id="photoTone" x1="0" y1="0" x2="1" y2="1">
        <stop offset="0" stop-color="#d9cfc4"/><stop offset=".5" stop-color="#b9a493"/><stop offset="1" stop-color="#e8e3de"/>
      </linearGradient>
      <linearGradient id="flame" x1="0" y1="0" x2="1" y2="0">
        <stop offset="0" stop-color="#f9a13a"/><stop offset=".6" stop-color="#f47a20"/><stop offset="1" stop-color="#e2322b"/>
      </linearGradient>
      <linearGradient id="footFlame" x1="0" y1="0" x2="1" y2="0">
        <stop offset="0" stop-color="#f47a20"/><stop offset="1" stop-color="#e8452b"/>
      </linearGradient>
    </defs>
    <rect class="header-band" x="0" y="0" width="1200" height="396" fill="var(--black)"/>
    <rect class="crowd-photo" x="0" y="396" width="1200" height="820" fill="url(#photoTone)" role="img" aria-label="Photo of a cheering group of happy adults raising their hands"/>
    <path class="corner-black" d="M740 396 C960 420 1120 520 1200 650 L1200 396 Z" fill="var(--black)"/>
    <path class="swoosh-back" d="M740 396 C960 420 1120 520 1200 650 L1200 690 C1110 560 950 450 720 400Z" fill="url(#flame)"/>
    <path class="lower-field" d="M0 1190 C300 1060 700 900 1200 700 L1200 2765 L0 2765Z" fill="var(--white)"/>
    <path class="swoosh-front" d="M0 1150 C300 1030 700 870 1200 650 L1200 720 C700 930 300 1080 0 1200Z" fill="url(#flame)"/>
    <path class="foot-light" d="M0 2735 C520 2725 1000 2580 1200 2290 L1200 2765 L0 2765Z" fill="var(--orange-light)"/>
    <path class="foot-band" d="M0 2765 C560 2750 1020 2630 1200 2360 L1200 2765Z" fill="url(#footFlame)"/>
  </svg>

  <div class="brand">MAPLEWOOD<span class="brand-sub">COMMUNITY SCHOOLS</span></div>

  <div class="tagline">
    <span class="greatest">greatest</span>
    <span class="fundraiser">FUNDRAISER</span>
    <span class="ever">ever!</span>
  </div>

  <svg class="offer-card" width="1200" height="1700" viewBox="0 0 1200 1700">
    <polygon points="145,1050 800,960 1128,1270 1128,1560 530,1600 300,1300 145,1265" fill="var(--white)" style="filter:drop-shadow(0 10px 12px var(--card-shadow))"/>
    <g fill="none" stroke="var(--orange-light)" stroke-width="3">
      <path d="M295 1207 L267 1437 L525 1456"/>
      <path d="M774 973 L921 990 L940 1272"/>
    </g>
    <polygon points="460,960 755,940 760,1105 480,1125" fill="var(--red)"/>
    <polygon points="820,1275 1128,1265 1128,1548 845,1555" fill="var(--red)"/>
  </svg>
  <div class="card-word card-donate">donate</div>
  <div class="card-amount amount-top"><small>$</small>25</div>
  <div class="card-word card-get">and you get</div>
  <div class="egift"><span class="egift-word">e-Gift</span><span class="egift-label">CARD</span></div>
  <div class="card-amount amount-bottom"><small>$</small>25</div>

  <a class="cta cta-red" href="#donate-25" aria-label="Click here: $25 for $25">
    <span class="cta-face">
      <span class="cta-label">CLIK HERE</span>
      <span class="cta-price price-one"><sup>$</sup>25</span>
      <span class="cta-for">FOR</span>
      <span class="cta-price price-two"><sup>$</sup>25</span>
    </span>
  </a>

  <p class="pitch">Simply donate $25 and<br>we give you $25 back in<br>e-Gift Cards for<br>restaurants in your area!</p>

  <ul class="benefits">
    <li><svg viewBox="0 0 24 24"><path d="M2 13 L9 21 L22 3 L9 15Z" fill="var(--tick)"/></svg>More than 500,000 deals available every day</li>
    <li><svg viewBox="0 0 24 24"><path d="M2 13 L9 21 L22 3 L9 15Z" fill="var(--tick)"/></svg>Local independent neughborhood restaurants</li>
    <li><svg viewBox="0 0 24 24"><path d="M2 13 L9 21 L22 3 L9 15Z" fill="var(--tick)"/></svg>Always available. Never expire.</li>
    <li><svg viewBox="0 0 24 24"><path d="M2 13 L9 21 L22 3 L9 15Z" fill="var(--tick)"/></svg>More than 62,000+ restaurants &amp; providers nationwide</li>
  </ul>

  <a class="cta cta-gold" href="#donate-30" aria-label="Click here: $30 for $50">
    <span class="cta-face">
      <span class="cta-label">CLIK HERE</span>
      <span class="cta-price price-one"><sup>$</sup>30</span>
      <span class="cta-for">FOR</span>
      <span class="cta-price price-two"><sup>$</sup>50</span>
    </span>
  </a>

  <h2 class="upsell-title">$30 for $50</h2>
  <p class="upsell-text">For only an extra $5 we will send<br>you an additional $25 e-Gift Card.</p>

  <div class="contact">
    <a href="#home">www.goodbites.org
      <svg viewBox="0 0 40 40"><circle cx="20" cy="20" r="17" fill="none" stroke="var(--white)" stroke-width="3"/><path d="M20 10 L30 19 L27 19 L27 29 L22 29 L22 23 L18 23 L18 29 L13 29 L13 19 L10 19Z" fill="var(--white)"/></svg>
    </a>
    <a href="#email">support@goodbites.org
      <svg viewBox="0 0 40 40"><circle cx="20" cy="20" r="17" fill="none" stroke="var(--white)" stroke-width="3"/><rect x="11" y="14" width="18" height="12" rx="1" fill="var(--white)"/><path d="M11 14 L20 21 L29 14" fill="none" stroke="var(--orange)" stroke-width="2"/></svg>
    </a>
  </div>
</div>
</body>
</html>
```